Bespoke Builders Business Card Design

We need a business card for an established builder of high quality bespoke homes in Auckland and Northland. We build and renovate homes collaboratively facilitating effective communication between owners, builders, architects, suppliers and tradespeople. We have never built or renovated a home that leaks or has faults. We only use reliable materials. We have never been sued or had legal action taken against us. We are honest builders of bespoke homes not group mass produced homes. Our niche market is in character homes. We practice sustainability and have built a lot of coastal property. We have been in business for over thirty years . We would like to see natural colors of the environment sand,sea and maybe vegetation . The design should communicate quality, sustainability,fair pricing, open communication and the originality of bespoke building. And the fact that the builder is registered.

Industry/Entity Type

Business

Contact Information for Business Card

Rowan Tellick Builders
Ph. 021583917
18 Kestrel Rd Harwood Bay Auckland 0814
PO Box 927 Mangawhai 0583

```html
<!DOCTYPE html>
<html lang="en">
<head>
<meta charset="utf-8">
<title>Rowan Tellick Builders — Business Card</title>
<link rel="stylesheet" href="https://fonts.googleapis.com/css2?family=Libre+Bodoni:wght@600&family=Open+Sans:wght@400&display=swap">
<style>
  :root {
    --backdrop: #e9e6e1;
    --card-white: #ffffff;
    --card-black: #000000;
    --accent-navy: #2c2f7c;
    --text-dark: #000000;
    --text-light: #ffffff;
    --card-shadow: 0 4px 10px rgba(0, 0, 0, 0.35);
  }
  * { box-sizing: border-box; margin: 0; padding: 0; }
  html, body {
    width: 1189px;
    height: 1200px;
    overflow: hidden;
    background: var(--backdrop);
  }
  .canvas {
    position: relative;
    width: 1189px;
    height: 1200px;
  }
  .card {
    position: absolute;
    left: 140px;
    width: 918px;
    height: 524px;
    overflow: hidden;
    box-shadow: var(--card-shadow);
  }
  .card--front { top: 45px; background: var(--card-white); }
  .card--back  { top: 624px; background: var(--card-black); }

  .card__swoosh {
    position: absolute;
    inset: 0;
    width: 918px;
    height: 524px;
  }
  .swoosh__dark  { fill: var(--card-black); }
  .swoosh__accent { fill: var(--accent-navy); }

  .company-name {
    position: absolute;
    left: 0;
    width: 100%;
    text-align: center;
    font-family: "Libre Bodoni", "Bodoni Moda", Georgia, serif;
    font-weight: 600;
    font-size: 70px;
    line-height: 1;
    letter-spacing: 0.5px;
    white-space: nowrap;
  }
  .card--front .company-name { top: 78px; color: var(--text-dark); }
  .card--back  .company-name { top: 226px; color: var(--text-light); }

  .contact {
    position: absolute;
    left: 0;
    width: 100%;
    text-align: center;
    color: var(--text-light);
    font-family: "Open Sans", "Segoe UI", Arial, sans-serif;
    font-weight: 400;
    letter-spacing: 0.6px;
  }
  .contact__phone {
    top: 355px;
    font-size: 30px;
    line-height: 1;
  }
  .contact__address {
    top: 412px;
    font-size: 29px;
    line-height: 42px;
  }
</style>
</head>
<body>
<main class="canvas">
  <section class="card card--front" aria-label="Business card front">
    <svg class="card__swoosh" viewBox="0 0 918 524" aria-hidden="true">
      <path class="swoosh__dark" d="M0,175 Q459,438 918,172 L918,524 L0,524 Z"/>
      <path class="swoosh__accent" d="M32,190 Q459,380 870,196 Q459,416 32,190 Z"/>
    </svg>
    <h1 class="company-name">Rowan Tellick Builders</h1>
    <p class="contact contact__phone">021583917</p>
    <p class="contact contact__address">18 Kestrel Rd Harwood Bay Auckland 0814<br>PO Box 927 Mangawhai 0583</p>
  </section>

  <section class="card card--back" aria-label="Business card back">
    <p class="company-name">Rowan Tellick Builders</p>
  </section>
</main>
</body>
</html>
```